Automotive eCommerce Business looking for a business card design

Looking for a clean and simple business card design. Our company name is "Brindle Auto" and we are a company specializing in the ecommerce sales of automotive parts, specifically for pick up trucks and large SUVs. Our company colours are red, black, and white.

Feel free to use the logo provided or create a new logo that you seem fit. Looking forward to your creative ideas!

Industry/Entity Type

Automotive

Contact Information for Business Card

We were thinking of a possibly two-sided design featuring just the logo and company name on one side, and personal information on the other side. Single sided designs will be considered as well.

Font styles to use
Serif
Sans Serif
Decorative

Colors
ec1f27
ffffff
000000

Requirements
Must have
• Space for employee's name, title, phone number and email address, along with the company address and website somewhere.

```html
<!DOCTYPE html>
<html lang="en">
<head>
<meta charset="utf-8">
<title>Brindle Auto — Business Card</title>
<link rel="stylesheet" href="https://fonts.googleapis.com/css2?family=Fira+Sans:wght@300;400;600&display=swap">
<style>
  :root {
    --brand-red: #c92a3a;
    --brand-red-deep: #a51d2b;
    --card-white: #ffffff;
    --paper-shade: #f1f1f1;
    --text-grey: #8c8c8c;
    --backdrop: #e6e2dc;
  }
  * { box-sizing: border-box; margin: 0; padding: 0; }
  html, body {
    width: 1200px; height: 1023px; overflow: hidden;
    background: var(--backdrop);
    font-family: "Fira Sans", Arial, sans-serif;
  }
  .sheet { position: relative; width: 1200px; height: 1023px; }
  .card {
    position: absolute; left: 215px; width: 770px; height: 440px;
    border-radius: 34px; overflow: hidden;
    box-shadow: 0 10px 26px rgba(0,0,0,0.18);
  }
  /* Front side */
  .card-front {
    top: 60px;
    background: linear-gradient(135deg, var(--card-white) 40%, var(--paper-shade));
  }
  .name-band {
    position: absolute; left: 0; top: 88px; width: 560px; height: 84px;
    background: var(--brand-red);
    padding: 12px 0 0 150px; color: var(--card-white);
  }
  .person-name { font-size: 36px; font-weight: 600; line-height: 1.05; letter-spacing: 0.5px; }
  .person-title { font-size: 19px; font-weight: 300; letter-spacing: 0.5px; }
  .front-brand {
    position: absolute; left: 580px; top: 112px;
    display: flex; align-items: center; gap: 10px;
    font-size: 28px; font-weight: 600; color: var(--brand-red); white-space: nowrap;
  }
  .brand-dot {
    width: 14px; height: 14px; border-radius: 50%; background: var(--brand-red);
  }
  .address {
    position: absolute; left: 204px; top: 218px;
    font-size: 21px; font-weight: 300; color: var(--text-grey); line-height: 1.25;
    letter-spacing: 0.4px;
  }
  .contact-list { position: absolute; left: 160px; top: 292px; list-style: none; }
  .contact-list li {
    display: flex; align-items: center; gap: 16px;
    font-size: 21px; font-weight: 300; color: var(--text-grey);
    height: 28px; letter-spacing: 0.4px;
  }
  .contact-icon {
    width: 26px; height: 24px; border-radius: 5px; background: var(--brand-red);
    display: flex; align-items: center; justify-content: center;
  }
  /* Back side */
  .card-back {
    top: 540px;
    background: linear-gradient(150deg, var(--brand-red) 30%, var(--brand-red-deep));
    color: var(--card-white);
  }
  .back-web {
    position: absolute; left: 60px; top: 46px;
    font-size: 20px; font-weight: 400; letter-spacing: 1.5px;
  }
  .back-brand {
    position: absolute; left: 0; right: 0; top: 190px; text-align: center;
    font-size: 60px; font-weight: 600; letter-spacing: 1px;
  }
</style>
</head>
<body>
<main class="sheet">
  <section class="card card-front" aria-label="Card front">
    <div class="name-band">
      <p class="person-name">Marcus Hale</p>
      <p class="person-title">Sales Director</p>
    </div>
    <p class="front-brand"><span class="brand-dot"></span>Brindle Auto</p>
    <p class="address">4820 Ridgeway Road, Suite 215<br>Fairhaven, 48210</p>
    <ul class="contact-list">
      <li><span class="contact-icon"><svg width="14" height="14" viewBox="0 0 24 24"><path fill="#fff" d="M6.6 10.8a15 15 0 0 0 6.6 6.6l2.2-2.2c.3-.3.7-.4 1-.2 1.1.4 2.3.6 3.6.6.6 0 1 .4 1 1V20c0 .6-.4 1-1 1A17 17 0 0 1 3 4c0-.6.4-1 1-1h3.5c.6 0 1 .4 1 1 0 1.3.2 2.5.6 3.6.1.3 0 .7-.2 1z"/></svg></span>555-014-2280</li>
      <li><span class="contact-icon"><svg width="14" height="14" viewBox="0 0 24 24"><path fill="#fff" d="M6 2h12v6H6zM3 9h18v9h-3v4H6v-4H3zm5 6v5h8v-5z"/></svg></span>555-014-2291</li>
      <li><span class="contact-icon"><svg width="14" height="12" viewBox="0 0 24 18"><path fill="#fff" d="M0 0h24v18H0zm2 2v1l10 7 10-7V2z"/></svg></span>mhale@brindleauto.com</li>
      <li><span class="contact-icon"><svg width="14" height="14" viewBox="0 0 24 24"><circle cx="12" cy="12" r="9" fill="none" stroke="#fff" stroke-width="2.5"/><path d="M3 12h18M12 3c-4 5-4 13 0 18M12 3c4 5 4 13 0 18" fill="none" stroke="#fff" stroke-width="2"/></svg></span>www.brindleauto.com</li>
    </ul>
  </section>

  <section class="card card-back" aria-label="Card back">
    <p class="back-web">www.brindleauto.com</p>
    <p class="back-brand">Brindle Auto</p>
  </section>
</main>
</body>
</html>
```